Mobile Fitness snd Therapy Business Card Design

I need a business card designed for my mobile fitness and therapy business.

Please view the images that I have uploaded. I like the simplicity of the design that I have attached. I adapted it with my information

Target Market(s)

Those seeking personal training, injury rehabilitation or massage therapy.

Industry/Entity Type

Business

Contact Information for Business Card

Derek Fulham - MSc, CAT(C), RMT, CSCS, Pn2
e-mail: derek@vantrelo.com
website: www.vantrelo.com
instagram: @derek_fulham

Font styles to use
Sans Serif

Colors
3176b5
0355a3

Requirements
Must have
• "Contact us to receive a FREE assessment"
• Services offered:
• Personal Training
• Golf Fitness
• Injury Rehab
• Massage Therapy
• Yoga
Nice to have
• Consistent colours with brand
• - Dark Blue: #232837
• - Blue: #5096f0
• Consistent look/feel with the website: www.vantrelo.com

```html
<!DOCTYPE html>
<html lang="en">
<head>
<meta charset="utf-8">
<title>Vantrelo Business Card</title>
<link rel="stylesheet" href="https://fonts.googleapis.com/css2?family=Arimo:wght@400;700&display=swap">
<style>
  :root {
    --canvas: #d8d8d8;
    --card-light: #ffffff;
    --card-dark: #232837;
    --blue-deep: #1d4fcf;
    --blue-brand: #3176b5;
    --blue-bright: #5096f0;
    --blue-soft: #8fbcf2;
    --blue-bar: #2a5fd6;
    --ink: #2a2d33;
    --white: #ffffff;
  }
  * { margin: 0; padding: 0; box-sizing: border-box; }
  html, body {
    width: 1200px; height: 900px; overflow: hidden;
    background: var(--canvas);
    font-family: "Arimo", Arial, sans-serif;
  }
  .stage { position: relative; width: 1200px; height: 900px; }
  .card {
    position: absolute; top: 306px; width: 440px; height: 271px;
    border-radius: 12px;
    box-shadow: 3px 4px 6px rgba(0,0,0,0.35);
    overflow: hidden;
  }
  .card--front { left: 149px; background: var(--card-light); }
  .card--back { left: 608px; background: var(--card-dark); }

  .accent-bar { position: absolute; top: 81px; width: 8px; height: 107px; }
  .accent-bar--left { left: 0; background: var(--blue-soft); }
  .accent-bar--right { right: 0; background: var(--blue-bar); }

  .identity { position: absolute; left: 22px; top: 80px; }
  .identity__name {
    font-size: 17px; font-weight: 700; color: var(--blue-deep);
    letter-spacing: 0.2px; line-height: 20px;
  }
  .identity__credentials {
    font-size: 13px; color: var(--blue-bright); margin-top: 1px;
  }
  .contact-list { list-style: none; margin-top: 23px; }
  .contact-list li {
    display: flex; align-items: center; gap: 4px;
    font-size: 13px; color: var(--ink); height: 18.5px;
  }
  .contact-list svg { width: 12px; height: 12px; flex: none; }

  .divider {
    position: absolute; left: 237px; top: 84px; width: 2px; height: 103px;
    background: var(--blue-brand);
  }

  .services { position: absolute; left: 261px; top: 82px; }
  .services__title {
    font-size: 13px; font-weight: 700; color: var(--blue-bright);
    letter-spacing: 0.3px;
  }
  .services__list { list-style: none; margin-top: 19px; }
  .services__list li {
    display: flex; align-items: center; gap: 5px;
    font-size: 11px; color: var(--ink); height: 14px;
  }
  .services__list li::before {
    content: ""; width: 8px; height: 8px; background: var(--blue-bright);
  }

  .cta {
    position: absolute; left: 0; right: 0; top: 235px; text-align: center;
    font-size: 11px; font-weight: 700; color: var(--blue-brand);
    letter-spacing: 0.2px;
  }

  .brand {
    position: absolute; left: 0; right: 0; top: 103px; text-align: center;
    color: var(--white);
  }
  .brand__name {
    font-size: 40px; font-weight: 700; letter-spacing: 4px; line-height: 46px;
  }
  .brand__tagline {
    font-size: 14px; font-weight: 700; letter-spacing: 2.3px; margin-top: 6px;
  }
</style>
</head>
<body>
<main class="stage">
  <section class="card card--front" aria-label="Business card front">
    <span class="accent-bar accent-bar--left"></span>
    <span class="accent-bar accent-bar--right"></span>

    <div class="identity">
      <h1 class="identity__name">DEREK FULHAM</h1>
      <p class="identity__credentials">MSc, CAT(C), RMT, CSCS, Pn2</p>
      <ul class="contact-list">
        <li>
          <svg viewBox="0 0 12 12" aria-hidden="true"><rect x="0.5" y="2" width="11" height="8" rx="1" fill="#1d4fcf"/><path d="M1 2.8 6 6.6 11 2.8" fill="none" stroke="#fff" stroke-width="1"/></svg>
          derek@vantrelo.com
        </li>
        <li>
          <svg viewBox="0 0 12 12" aria-hidden="true"><circle cx="6" cy="6" r="5.5" fill="#1d4fcf"/><path d="M0.8 6h10.4M6 0.5c-2.4 2.8-2.4 8.2 0 11M6 0.5c2.4 2.8 2.4 8.2 0 11" fill="none" stroke="#fff" stroke-width="0.8"/></svg>
          www.vantrelo.com
        </li>
        <li>
          <svg viewBox="0 0 12 12" aria-hidden="true"><circle cx="6" cy="6" r="5.5" fill="#1d4fcf"/></svg>
          @derek_fulham
        </li>
      </ul>
    </div>

    <span class="divider"></span>

    <div class="services">
      <h2 class="services__title">SERVICES OFFERED:</h2>
      <ul class="services__list">
        <li>Personal Training</li>
        <li>Golf Fitness</li>
        <li>Injury Rehab</li>
        <li>Massage Therapy</li>
        <li>Yoga</li>
      </ul>
    </div>

    <p class="cta">CONTACT US TO RECEIVE A FREE ASSESSMENT</p>
  </section>

  <section class="card card--back" aria-label="Business card back">
    <div class="brand">
      <p class="brand__name">VANTRELO</p>
      <p class="brand__tagline">NUTRITION - FITNESS - HEALTH</p>
    </div>
  </section>
</main>
</body>
</html>
```